Custom unique Stationary design for Logistics company

We need a custom, unique , elegant and luxurious full stationary design using our new logo, following these guidelines:
1- Business card: double sided, both sides uses the navy blue as the background main color (same as the code of the navy blue used in our logo).
2- envelope and folder: also use the same navy blue as the main background color.
3- book cover( notepad cover) : same thing with the navy blue
4- letterhead: feel free to use the combination of the colors in our logo.
5- rest of the items are up to your creativity

Target Market(s)

corporates and other businesses

Industry/Entity Type

Logistics and heavy machines contractors

Requirements
Must have
• Letterhead, business card, envelope, notepad cover, paper, file
Nice to have
• navy blue to be main background color for business card, envelope, notepad cover

```html
<!DOCTYPE html>
<html lang="en">
<head>
<meta charset="utf-8">
<title>Kestrel Envelope Stationery</title>
<link href="https://fonts.googleapis.com/css2?family=Montserrat:wght@400;500;800&display=swap" rel="stylesheet">
<style>
  :root {
    --navy: #064c70;
    --orange: #e65a2e;
    --paper: #f7f6f6;
    --paper-edge: #efeeee;
    --backdrop: #d1d0d0;
    --ink: #1a1a1a;
    --tag-grey: #8f9398;
  }
  html, body {
    margin: 0;
    padding: 0;
    width: 1200px;
    height: 1050px;
    overflow: hidden;
    background: var(--backdrop);
    font-family: "Montserrat", sans-serif;
  }
  .canvas {
    position: relative;
    width: 1200px;
    height: 1050px;
  }
  .envelope {
    position: absolute;
    left: 145px;
    width: 910px;
    height: 390px;
    background: radial-gradient(ellipse at 50% 55%, #ffffff 0%, var(--paper) 45%, var(--paper-edge) 100%);
    overflow: hidden;
  }
  .envelope--back { top: 105px; }
  .envelope--front { top: 556px; }
  .envelope svg.art {
    position: absolute;
    inset: 0;
  }
  .flap-brand {
    position: absolute;
    left: 0;
    right: 0;
    top: 30px;
    text-align: center;
    color: #ffffff;
  }
  .brand-name {
    font-weight: 800;
    letter-spacing: 2px;
    line-height: 1;
  }
  .flap-brand .brand-name { font-size: 44px; }
  .flap-brand .brand-tag {
    margin-top: 10px;
    font-size: 7px;
    font-weight: 800;
    letter-spacing: 0.6px;
    text-transform: uppercase;
  }
  .front-brand {
    position: absolute;
    left: 43px;
    top: 48px;
    width: 240px;
  }
  .front-brand .brand-name {
    font-size: 70px;
    color: var(--navy);
    display: flex;
    align-items: center;
    gap: 10px;
  }
  .brand-dot {
    width: 12px;
    height: 12px;
    border-radius: 50%;
    background: var(--orange);
    flex: none;
  }
  .front-brand .brand-tag {
    margin-top: 14px;
    font-size: 9.5px;
    font-weight: 800;
    letter-spacing: 0.5px;
    text-transform: uppercase;
    color: var(--tag-grey);
  }
  .return-address {
    position: absolute;
    left: 41px;
    top: 184px;
    margin: 0;
    font-size: 15.5px;
    font-weight: 500;
    line-height: 20px;
    color: var(--ink);
    font-style: normal;
  }
</style>
</head>
<body>
<main class="canvas">

  <section class="envelope envelope--back" aria-label="Envelope back">
    <svg class="art" width="910" height="390" viewBox="0 0 910 390" aria-hidden="true">
      <path class="flap" fill="var(--navy)" d="M0,0 H910 L885,90 Q870,131 825,131 H85 Q40,131 25,90 Z"/>
    </svg>
    <div class="flap-brand">
      <div class="brand-name">KESTREL</div>
      <div class="brand-tag">Heavy Freight Logistics</div>
    </div>
  </section>

  <section class="envelope envelope--front" aria-label="Envelope front">
    <svg class="art" width="910" height="390" viewBox="0 0 910 390" aria-hidden="true">
      <path class="wave-navy" fill="var(--navy)" d="M0,345 C300,372 660,352 910,184 L910,390 L0,390 Z"/>
      <path class="wave-orange" fill="var(--orange)" d="M0,319 C360,372 690,345 864,203 C690,334 350,388 0,341 Z"/>
    </svg>
    <div class="front-brand">
      <div class="brand-name"><span class="brand-dot"></span>KESTREL</div>
      <div class="brand-tag">Heavy Freight Logistics</div>
    </div>
    <address class="return-address">
      1420 Harbor Line Rd, Unit 310<br>
      Brampton, ON L6T 3K9
    </address>
  </section>

</main>
</body>
</html>
```